Oakmere Animal Care Group of Central Pennsylvania

I need a business card design for a new company in Harrisburg PA called "Animal Care Oakmere Group of Central PA". I will be providing relief services for veterinarians who need coverage during vacations; sick/maternity leave, etc. I would like to see the veterinarian symbol incorporated in the design in combination with animals (dogs /cats/birds/reptiles an pocket pets). Include My full name: Tomás R. Quintaval DVM, MLAS, BS. Also include my e mail (dvmtrq@mailbrook.net) and phone number 5552846017

Target Market(s)

Small Animal Veterinarian, practice owner

Industry/Entity Type

Business

Contact Information for Business Card

Oakmere Animal Care Group of Central PA

Font styles to use
Script

Requirements
Must have
• Veterinarian caduceus (see image) and Small animals (pets) within the logo.
Nice to have
• Give a sense of relaxation (vacationing)
Should not have
• Large animals, i.e. horses, cows, zoo animals...

```html
<!DOCTYPE html>
<html lang="en">
<head>
<meta charset="utf-8">
<title>Animal Care Oakmere Group of Central PA — Business Card</title>
<link rel="stylesheet" href="https://fonts.googleapis.com/css2?family=Cinzel:wght@600&family=Crimson+Text&family=Sofia&display=swap">
<style>
  :root {
    --stage: #e9e7e3;
    --paper: #f7f7f6;
    --paper-shade: #e4e4e4;
    --band: #0d0d0d;
    --band-light: #1c1c1c;
    --ink: #1a1a1a;
    --accent: #c0262b;
    --on-band: #f4f4f4;
    --rule: #bdbdbd;
  }
  * { box-sizing: border-box; margin: 0; padding: 0; }
  html, body {
    width: 1200px; height: 892px; overflow: hidden;
    background: var(--stage);
  }
  .canvas {
    width: 1200px; height: 892px;
    display: flex; align-items: center; justify-content: center;
  }
  .card {
    position: relative;
    width: 1050px; height: 600px;
    background: linear-gradient(180deg, var(--paper) 0%, var(--paper-shade) 54%);
    overflow: hidden;
    box-shadow: 0 10px 30px rgba(0,0,0,.25);
  }
  .band {
    position: absolute; left: 0; right: 0; top: 325px; bottom: 0;
    background: linear-gradient(180deg, var(--band-light), var(--band));
  }
  .brand {
    position: absolute; left: 50px; top: 200px;
    display: flex; align-items: center; gap: 18px;
  }
  .brand-dot {
    width: 84px; height: 84px; border-radius: 50%;
    border: 6px solid var(--accent);
    flex: none;
  }
  .brand-name {
    font-family: "Cinzel", serif; font-weight: 600;
    font-size: 20px; line-height: 1.3; letter-spacing: .3px;
    color: var(--ink);
    white-space: nowrap;
  }
  .pets-photo {
    position: absolute; left: 600px; top: 170px;
    width: 410px; height: 155px;
    background: linear-gradient(90deg, #cbbfa8 0%, #6e5a3e 30%, #d9d6cf 60%, #9db06a 100%);
    opacity: .85;
  }
  .holder-name {
    position: absolute; left: 50px; top: 430px;
    font-family: "Sofia", cursive; font-size: 54px;
    color: var(--on-band);
    white-space: nowrap;
  }
  .contact {
    position: absolute; left: 590px; top: 362px; right: 0;
  }
  .contact-rule {
    height: 2px; background: var(--rule); margin-bottom: 24px;
  }
  .contact-line {
    font-family: "Crimson Text", serif; font-size: 30px;
    color: var(--on-band); letter-spacing: .5px; line-height: 1.5;
  }
  .edge-rule {
    position: absolute; right: 34px; top: 325px; bottom: 0;
    width: 2px; background: rgba(255,255,255,.35);
  }
</style>
</head>
<body>
<main class="canvas">
  <article class="card">
    <div class="band"></div>
    <div class="pets-photo" role="img" aria-label="Photo of pets in a row: a shepherd dog, a bulldog, a cat, a rabbit, small birds, a lizard and a parrot"></div>
    <div class="brand">
      <span class="brand-dot"></span>
      <p class="brand-name">Animal Care Oakmere Group<br>of Central PA</p>
    </div>
    <p class="holder-name">Tomás R. Quintaval</p>
    <div class="contact">
      <div class="contact-rule"></div>
      <p class="contact-line">5552846017</p>
      <p class="contact-line">dvmtrq@mailbrook.net</p>
    </div>
    <div class="edge-rule"></div>
  </article>
</main>
</body>
</html>
```